Personal Injury Lawyer Billboard

I would like a design created featuring the image of the lawyer centered in the middle of the design.
To the left of the lawyer's image it should read "INJURED?"
To the right of the lawyer's image, it should read "CALL DEAN!"
Under Call Dean, include the phone number 318-555-0187.
At the bottom of the design include the lawyers information "Dean Marlowe Accident & Injury Lawyers"
PLEASE REMOVED THE BACKGROUND IMAGERY OF THE PHOTO SUBMITTED. Also, the colors for this design should match the colors shown in the logo (navy, white and relective soft gold). Please use those color combinations in ways that best stand out.

```html
<!DOCTYPE html>
<html lang="en">
<head>
<meta charset="utf-8">
<title>Dean Marlowe Accident &amp; Injury Lawyers – Billboard</title>
<link rel="stylesheet" href="https://fonts.googleapis.com/css2?family=Bebas+Neue&family=Montserrat:wght@700;800&display=swap">
<style>
  :root {
    --navy: #0b1c45;
    --white: #ffffff;
    --gold-light: #e2c65e;
    --gold-deep: #bf922e;
    --gold-text: #f0c132;
  }
  html, body {
    margin: 0;
    padding: 0;
    width: 1200px;
    height: 450px;
    overflow: hidden;
    background: var(--navy);
  }
  .billboard {
    display: block;
    width: 1200px;
    height: 450px;
  }
  .headline {
    font-family: "Bebas Neue", "Oswald", sans-serif;
  }
  .firm-name,
  .phone,
  .tagline {
    font-family: "Montserrat", "Helvetica Neue", Arial, sans-serif;
  }
  .firm-name { fill: var(--white); font-weight: 800; }
  .phone { fill: var(--navy); font-weight: 800; }
  .tagline { font-weight: 800; fill: var(--white); }
  .tagline .tagline-name { fill: var(--gold-text); }
</style>
</head>
<body>
<svg class="billboard" viewBox="0 0 1200 450" xmlns="http://www.w3.org/2000/svg">
  <defs>
    <linearGradient id="gold" x1="0" y1="0" x2="0" y2="1">
      <stop offset="0" stop-color="var(--gold-light)"/>
      <stop offset="1" stop-color="var(--gold-deep)"/>
    </linearGradient>
    <linearGradient id="portrait-tones" x1="0" y1="0" x2="0" y2="1">
      <stop offset="0" stop-color="#3a2c2a"/>
      <stop offset="0.25" stop-color="#8a6552"/>
      <stop offset="0.4" stop-color="#e9e9ee"/>
      <stop offset="0.55" stop-color="#1f3166"/>
      <stop offset="1" stop-color="#13224d"/>
    </linearGradient>
  </defs>

  <!-- backgrounds -->
  <rect class="panel-navy" x="0" y="0" width="1200" height="450" fill="var(--navy)"/>
  <rect class="panel-white" x="575" y="0" width="625" height="301" fill="var(--white)"/>

  <!-- lawyer portrait area -->
  <path class="portrait" role="img" aria-label="Cut-out photo of attorney Dean Marlowe in a navy suit and green tie, fist raised"
        d="M416 450 L418 300 Q425 210 500 185 L515 160 Q498 120 496 60 Q500 0 548 0 Q598 0 601 60 Q600 130 590 165 Q650 180 690 200 Q725 230 725 330 L725 450 Z"
        fill="url(#portrait-tones)"/>

  <!-- left headline -->
  <text class="headline headline-injured" x="39" y="197" font-size="200"
        textLength="410" lengthAdjust="spacingAndGlyphs" fill="url(#gold)">INJURED</text>

  <!-- firm name -->
  <text class="firm-name firm-name-main" x="42" y="294" font-size="44"
        textLength="371" lengthAdjust="spacingAndGlyphs">DEAN MARLOWE</text>
  <text class="firm-name firm-name-sub" x="42" y="356" font-size="26"
        textLength="371" lengthAdjust="spacingAndGlyphs">ACCIDENT &amp; INJURY LAWYERS</text>

  <!-- right headline -->
  <text class="headline headline-call" x="655" y="177" font-size="178"
        textLength="507" lengthAdjust="spacingAndGlyphs" fill="url(#gold)">CALL DEAN!</text>

  <!-- phone -->
  <text class="phone" x="732" y="279" font-size="72"
        textLength="443" lengthAdjust="spacingAndGlyphs">318-555-0187</text>

  <!-- tagline -->
  <text class="tagline" x="749" y="353" font-size="34"
        textLength="412" lengthAdjust="spacingAndGlyphs"><tspan class="tagline-name">Dean Marlowe</tspan> Accident</text>
  <text class="tagline" x="749" y="399" font-size="34"
        textLength="285" lengthAdjust="spacingAndGlyphs">&amp; Injury Lawyers</text>
</svg>
</body>
</html>
```